2 x Digitize Logo | 2 x Business Cards | 2 x Fridge Magnets

We require 6 deliverables:
1. Residential logo redrawn (same just high quality for large print format).
2. Corporate logo redrawn (minor changes to wording and high quality for large print format).
3. New business card design for Furniture Removals (residential)
4. New business card design for Corporate Relocations (business)
5. New Fridge magnet for Furniture removals (residential)
6. New fridge magnet for Corporate Relocations (business)
1. Residential Logo
a. We require the logo to be translated into a high quality digital image with no modifications.
(see attached resilogo.jpg)
2. Residential Logo
a. We require the logo to be edited (add the word corporate relocations) be translated into a high quality digital image.
(see attached corplogo.jpg)
3. Using the resilogo please make a new business card for our business.
a. Please see the web site https://www.larkbendcarters.com.au for colours and inspiration.
b. The residential business card needs the following information:
i. Business Name (using the residential logo).
ii. Free Call: 1800 LB Move (the L, B and Cart much be the same colour as the logo).
iii. Website: www.LarkbendCarters.com.au
iv. Address: 4/17 Ormsdale Court, VIC 3264
v. Email: cart@LarkbendCarters.com.au
vi. backof Card:
Review our service
www.PennantOrbit.com.au
Services: Local, Country, Interstate | Furniture Removals | Piano, Billiard Tables & Antiques
4. Using the corplogo please make a new business card for our business.
b. The corporate business card needs the following information:
i. Business Name (using the corporate logo).
v. Email: corporate@LarkbendCarters.com.au
vi. Back of Card:
Review our service
www.PennantOrbit.com.au
Services: Corporate relocations | Office equipment moves | Packing Service | Packing Materials
5. Using the resilogo please make a new fridge magent for our business.
b. The residential fidge magnet needs the following information:
iv. Services: Local, Country, Interstate | Furniture Removals | Piano, Billiard Tables & Antiques
6. Using the corplogo please make a new fridge magent for our business.
b. The corporate fidge magnet needs the following information:
iv. Services: Local, Country, Interstate | Corporate relocations
Target Market(s)
Residential Furniture Removals and Corporate Office relocations
Industry/Entity Type
Business
Contact Information for Business Card
Please see full brief for six items required
Requirements
Must have
- Clean simple, easy to read
Nice to have
- fresh, stand out, eye catching
Should not have
- plain, standard, boring, general

```html
<!DOCTYPE html>
<html lang="en">
<head>
<meta charset="utf-8">
<title>Larkbend Carters – Business Cards</title>
<link href="https://fonts.googleapis.com/css2?family=Oswald:wght@500;700&family=Roboto+Condensed:wght@400;500&family=Open+Sans:wght@400;600&display=swap" rel="stylesheet">
<style>
  :root{
    --backdrop:#cbcbcb;
    --card-dark:#2a2a2a;
    --card-light:#ffffff;
    --brand-orange:#f0a000;
    --brand-red:#dc241f;
    --brand-green:#16913a;
    --ink:#2b2b2b;
    --ink-light:#f2f2f2;
    --rule:#9a9a9a;
  }
  *{box-sizing:border-box;margin:0;padding:0}
  html,body{width:1200px;height:782px;overflow:hidden;background:var(--backdrop)}
  .sheet{position:relative;width:1200px;height:782px}
  .card{position:absolute;width:418px;height:252px;box-shadow:6px 8px 10px rgba(0,0,0,.28)}
  .card--back{left:165px;background:var(--card-dark);color:var(--ink-light)}
  .card--front{left:617px;background:var(--card-light);color:var(--ink)}
  .row-residential{top:118px}
  .row-corporate{top:411px}

  .brand-name{position:absolute;left:0;right:0;text-align:center;font-family:"Oswald",sans-serif;font-weight:700;color:var(--brand-orange);text-transform:uppercase;letter-spacing:.5px;line-height:1}
  .brand-name--large{top:56px;font-size:36px}
  .brand-name--medium{top:75px;font-size:20px}
  .brand-tag{position:absolute;left:0;right:0;text-align:center;font-family:"Open Sans",sans-serif;font-size:9.5px;color:var(--brand-green);letter-spacing:.3px}

  .review{position:absolute;left:0;right:0;text-align:center;font-family:"Open Sans",sans-serif}
  .review__label{display:flex;align-items:center;justify-content:center;gap:12px;font-size:11.5px;color:var(--ink-light)}
  .review__label::before,.review__label::after{content:"";width:88px;height:2px;background:linear-gradient(90deg,transparent,var(--rule) 30%,var(--rule) 70%,transparent)}
  .review__url{font-size:15px;margin-top:3px;color:var(--ink-light)}
  .review__url .c1{color:var(--brand-orange);font-weight:600}
  .review__url .c2{color:var(--brand-green);font-weight:600}

  .services{position:absolute;left:0;right:0;top:224px;text-align:center;font-family:"Roboto Condensed",sans-serif;font-weight:500;font-size:10.5px;color:var(--ink-light);white-space:nowrap}
  .services .sep{color:var(--brand-orange);margin:0 4px}

  .person{position:absolute;left:19px;top:24px}
  .person__name{font-family:"Oswald",sans-serif;font-weight:700;font-size:17px;color:var(--brand-red);line-height:1.1;text-transform:uppercase}
  .person__role{font-family:"Roboto Condensed",sans-serif;font-size:9.5px;margin-top:2px}

  .contact{position:absolute;left:19px;top:165px;font-family:"Roboto Condensed",sans-serif;font-size:10px;line-height:15px}
  .contact__item{display:flex;align-items:center;gap:8px}
  .contact__item svg{width:10px;height:10px}
  .contact__address{margin-top:4px}
  .web .c1{color:var(--brand-orange)}
  .web .c2{color:var(--brand-red)}
  .web .c3{color:var(--brand-green)}

  .front-brand{position:absolute;left:230px;width:170px;text-align:center;font-family:"Oswald",sans-serif;font-weight:700;color:var(--brand-green);text-transform:uppercase;line-height:1}
  .front-brand--res{top:165px;font-size:26px}
  .front-brand--corp{top:186px;font-size:17px}
  .front-brand .brand-sub{display:block;font-family:"Open Sans",sans-serif;font-weight:400;font-size:8.5px;margin-top:4px}
</style>
</head>
<body>
<main class="sheet">

  <section class="card card--back row-residential">
    <div class="brand-name brand-name--large">Larkbend Carters</div>
    <div class="review" style="top:140px">
      <div class="review__label">Review our service</div>
      <div class="review__url">www.<span class="c1">Pennant</span><span class="c2">Orbit</span>.com.au</div>
    </div>
    <div class="services">Local, Country, Interstate<span class="sep">|</span>Furniture Removals<span class="sep">|</span>Piano, Billiard Tables &amp; Antiques</div>
  </section>

  <section class="card card--front row-residential">
    <div class="person">
      <div class="person__name">Dana Whitlow</div>
      <div class="person__role">Managing Director</div>
    </div>
    <div class="contact">
      <div class="contact__item"><svg viewBox="0 0 10 10"><path d="M1 4c0-2 2-3 4-3s4 1 4 3l-2 .6-.4-1.4H3.4L3 4.6z M2 9h6l-.8-4H2.8z" fill="var(--brand-green)"/></svg>Free Call: 1800 LB</div>
      <div class="contact__item"><svg viewBox="0 0 10 10"><rect x="0.5" y="2" width="9" height="6.5" fill="var(--brand-red)"/><path d="M.5 2L5 5.6 9.5 2" stroke="#fff" stroke-width=".9" fill="none"/></svg>cart@larkbendcarters.com.au</div>
      <div class="contact__item"><svg viewBox="0 0 10 10"><circle cx="5" cy="5" r="4.3" fill="none" stroke="var(--brand-green)" stroke-width="1"/><path d="M.7 5h8.6M5 .7v8.6M2.4 2.6h5.2M2.4 7.4h5.2" stroke="var(--brand-green)" stroke-width=".8"/></svg><span class="web">www.<span class="c1">Larkbend</span><span class="c3">Carters</span>.com.au</span></div>
      <div class="contact__address">4/17 Ormsdale Court, VIC 3264</div>
    </div>
    <div class="front-brand front-brand--res">Larkbend<br>Carters</div>
  </section>

  <section class="card card--back row-corporate">
    <div class="brand-name brand-name--medium">Larkbend Carters</div>
    <div class="brand-tag" style="top:101px">CORPORATE RELOCATIONS</div>
    <div class="review" style="top:177px">
      <div class="review__label">Review our service</div>
      <div class="review__url">www.<span class="c1">Pennant</span><span class="c2">Orbit</span>.com.au</div>
    </div>
    <div class="services">Corporate relocations<span class="sep">|</span>Office equipment moves<span class="sep">|</span>Packing Service<span class="sep">|</span>Packing Materials</div>
  </section>

  <section class="card card--front row-corporate">
    <div class="person">
      <div class="person__name">Dana Whitlow</div>
      <div class="person__role">Managing Director</div>
    </div>
    <div class="contact">
      <div class="contact__item"><svg viewBox="0 0 10 10"><path d="M1 4c0-2 2-3 4-3s4 1 4 3l-2 .6-.4-1.4H3.4L3 4.6z M2 9h6l-.8-4H2.8z" fill="var(--brand-green)"/></svg>Free Call: 1800 LB</div>
      <div class="contact__item"><svg viewBox="0 0 10 10"><rect x="0.5" y="2" width="9" height="6.5" fill="var(--brand-red)"/><path d="M.5 2L5 5.6 9.5 2" stroke="#fff" stroke-width=".9" fill="none"/></svg>cart@larkbendcarters.com.au</div>
      <div class="contact__item"><svg viewBox="0 0 10 10"><circle cx="5" cy="5" r="4.3" fill="none" stroke="var(--brand-green)" stroke-width="1"/><path d="M.7 5h8.6M5 .7v8.6M2.4 2.6h5.2M2.4 7.4h5.2" stroke="var(--brand-green)" stroke-width=".8"/></svg><span class="web">www.<span class="c1">Larkbend</span><span class="c3">Carters</span>.com.au</span></div>
      <div class="contact__address">4/17 Ormsdale Court, VIC 3264</div>
    </div>
    <div class="front-brand front-brand--corp">Larkbend Carters<span class="brand-sub">CORPORATE RELOCATIONS</span></div>
  </section>

</main>
</body>
</html>
```